Coastline Premier Retreats Business Card Design

Design a business card for Coastline Premier Retreats. Look at the website for colors and reference. Card should have logo, name, title, office number, mobile number, email, URL and a tagline like, "Luxury Hotel & Resort Email Marketing" (This might change).

https://www.coastlinepremierretreats.example

The rest I will leave up to your imagination.

Contact Information for Business Card

Logo, name, title, office number, mobile number, email, URL and a tagline like, "Luxury Hotel & Resort Email Marketing" (This might change).

```html
<!DOCTYPE html>
<html lang="en">
<head>
<meta charset="utf-8">
<title>Coastline Premier Retreats – Business Card</title>
<link href="https://fonts.googleapis.com/css2?family=Open+Sans:wght@400;600;700&display=swap" rel="stylesheet">
<style>
  :root {
    --page-bg: #dcdddf;
    --card-cream: #fffef4;
    --brand-orange: #f47524;
    --brand-orange-deep: #e0641a;
    --ink: #111111;
    --rule: #333333;
    --shadow: rgba(0,0,0,0.28);
  }
  * { box-sizing: border-box; margin: 0; padding: 0; }
  html, body { width: 1200px; height: 780px; overflow: hidden; }
  body {
    background: var(--page-bg);
    font-family: "Open Sans", Arial, sans-serif;
    position: relative;
  }
  .card {
    position: absolute;
    top: 225px;
    width: 525px;
    height: 300px;
    box-shadow: 0 10px 26px var(--shadow);
    overflow: hidden;
  }

  /* Front */
  .card-front { left: 50px; background: var(--card-cream); }
  .front-brand {
    position: absolute;
    left: 34px; top: 92px;
    width: 200px;
    display: flex; align-items: center; gap: 10px;
  }
  .brand-square {
    flex: 0 0 18px; height: 18px;
    background: var(--brand-orange);
  }
  .brand-name {
    font-weight: 700;
    font-size: 21px;
    line-height: 1.15;
    color: var(--ink);
    text-transform: uppercase;
    letter-spacing: 0.5px;
  }
  .front-divider {
    position: absolute;
    left: 262px; top: 52px;
    width: 1px; height: 150px;
    background: var(--rule);
  }
  .front-details {
    position: absolute;
    left: 285px; top: 40px;
    width: 230px;
  }
  .person-name { font-size: 25px; font-weight: 700; line-height: 1.1; }
  .person-first { color: var(--brand-orange); }
  .person-last { color: var(--ink); }
  .person-title { font-size: 13px; font-weight: 600; color: var(--ink); margin: 3px 0 12px; }
  .contact-list { list-style: none; }
  .contact-item {
    display: flex; align-items: center; gap: 7px;
    font-size: 11.5px; line-height: 19px; color: var(--ink);
    white-space: nowrap;
  }
  .contact-icon { width: 11px; height: 11px; flex: 0 0 11px; }
  .tagline-band {
    position: absolute;
    left: 0; right: 0; bottom: 16px;
    height: 34px;
    background: var(--brand-orange);
    display: flex; align-items: center; justify-content: center;
  }
  .tagline {
    color: #ffffff; font-size: 13.5px; letter-spacing: 0.3px;
  }

  /* Back */
  .card-back {
    left: 625px; background: var(--brand-orange);
    display: flex; align-items: center; justify-content: center;
  }
  .back-brand {
    display: flex; align-items: center; gap: 14px;
  }
  .back-brand .brand-square { flex-basis: 26px; height: 26px; background: var(--brand-orange-deep); }
  .back-brand .brand-name {
    color: var(--brand-orange-deep);
    font-size: 30px; width: 330px;
  }
</style>
</head>
<body>

<section class="card card-front" aria-label="Business card front">
  <div class="front-brand">
    <span class="brand-square"></span>
    <span class="brand-name">Coastline Premier Retreats</span>
  </div>

  <div class="front-divider"></div>

  <div class="front-details">
    <h1 class="person-name"><span class="person-first">Marina</span> <span class="person-last">Kovalova</span></h1>
    <p class="person-title">Co-Founder</p>
    <ul class="contact-list">
      <li class="contact-item">
        <svg class="contact-icon" viewBox="0 0 12 12"><path d="M2.5 1 L4.5 1 L5 3.5 L3.8 4.4 Q4.8 6.8 7.6 8.2 L8.5 7 L11 7.5 L11 9.5 Q11 11 9.5 11 Q1 10 1 2.5 Q1 1 2.5 1Z" fill="#f47524"/></svg>
        (555) 014-2758
      </li>
      <li class="contact-item">
        <svg class="contact-icon" viewBox="0 0 12 12"><rect x="3" y="0.8" width="6" height="10.4" rx="1" fill="none" stroke="#f47524" stroke-width="1.2"/><circle cx="6" cy="9.4" r="0.6" fill="#f47524"/></svg>
        (555) 014-7777
      </li>
      <li class="contact-item">
        <svg class="contact-icon" viewBox="0 0 12 12"><circle cx="6" cy="6" r="5" fill="none" stroke="#f47524" stroke-width="1.2"/><ellipse cx="6" cy="6" rx="2.2" ry="5" fill="none" stroke="#f47524"/><line x1="1" y1="6" x2="11" y2="6" stroke="#f47524"/></svg>
        www.coastlinepremierretreats.example
      </li>
      <li class="contact-item">
        <svg class="contact-icon" viewBox="0 0 12 12"><rect x="0.8" y="2.2" width="10.4" height="7.6" fill="#f47524"/><path d="M0.8 2.2 L6 6.5 L11.2 2.2" fill="none" stroke="#fff" stroke-width="1"/></svg>
        info@coastlinepremierretreats.example
      </li>
    </ul>
  </div>

  <div class="tagline-band">
    <p class="tagline">Luxury Hotel &amp; Resort Email Marketing</p>
  </div>
</section>

<section class="card card-back" aria-label="Business card back">
  <div class="back-brand">
    <span class="brand-square"></span>
    <span class="brand-name">Coastline Premier Retreats</span>
  </div>
</section>

</body>
</html>
```